Email PDF Guide for Harbowline

We are an online professional services website which helps start ups and small businesses gain access to the R&D tax incentive.

We want to educate businesses across multiple industries to understand what they need to do to access this tax incentive, with information relevant to their industry. We need a designer to pull together and design images and relevant visuals for a downloadable guide. Please note - we will provide all the content for this, your job is to pull this into a stylised guide, which is inviting to our audience and compliment the words with imagery.

We are looking to produce 12 guides in total but will start with one to confirm design and style. Then follow up with remaining 11 industries.

First industry: Technology and Software

To get a sense for what we do our site is: https://www.harbowline.com/

Very interested to hear what the community comes up with to create something visually engaging and relevant to our site and message.

Target Market(s)

Start up founders and entrepreneurs in technology industry. Average age 35.

Industry/Entity Type

Information Technology

Font styles to use
Other font styles liked:
• Proxima Nova

Requirements
Must have
• - Guide needs to be minimum of 8 pages, content currently totals 5 word pages.
• - The format needs to be editable on standard Google or Microsoft products then formatted into PDF, so we can make text changes at later dates (can discuss this criteria if difficult)
• - Font is Proxima Nova
• - Colours and gradients can be found here: http://jadlisk.glenvaro.com/
• - Colour selection should be:
• * Main palette = #ff7c14 , #ffa800 , #fc4e78
• * Gray palette = #cccccc , #c1d1d9 , #f5f7f9 , #080808 , #2d3338 , #666666 , #6f7c82 , #999999
Nice to have
• Play with the title for best design format.
• Happy with one of the following options:
• - R&D in the Technology Industry
• - What you need to know about R&D in Technologu

```html
<!DOCTYPE html>
<html lang="en">
<head>
<meta charset="utf-8">
<title>Technology Development – Harbowline Guide</title>
<link href="https://fonts.googleapis.com/css2?family=Roboto:ital,wght@0,400;0,700;1,700&display=swap" rel="stylesheet">
<style>
  :root {
    --page-bg: #ffffff;
    --rule-gray: #999999;
    --brand-ink: #2d3338;
    --label-gray: #666666;
    --title-orange: #f7931e;
    --byline-ink: #2d3338;
    --art-coral: #e27a55;
    --art-red: #d9502f;
    --art-brown: #9a6e5a;
    --art-salmon: #e4875e;
  }
  * { margin: 0; padding: 0; box-sizing: border-box; }
  html, body { width: 844px; height: 1200px; overflow: hidden; background: var(--page-bg); }
  .guide-cover {
    position: relative;
    width: 844px;
    height: 1200px;
    overflow: hidden;
    font-family: "Roboto", Arial, sans-serif;
    background: var(--page-bg);
  }
  .top-rule {
    position: absolute; left: 0; top: 0; width: 100%; height: 3px;
    background: var(--rule-gray);
  }
  .partner-name {
    position: absolute; left: 26px; top: 66px;
    font-weight: 400; font-size: 34px; color: var(--brand-ink);
  }
  .product-name {
    position: absolute; left: 188px; top: 80px;
    font-weight: 400; font-size: 34px; color: var(--label-gray);
    line-height: 1;
  }
  .title-block {
    position: absolute; left: 0; top: 354px; width: 100%;
    text-align: center; color: var(--title-orange);
  }
  .cover-title { font-weight: 400; font-size: 66px; line-height: 1; letter-spacing: 0.5px; }
  .cover-subtitle { font-weight: 400; font-size: 50px; line-height: 1; margin-top: 16px; }
  .byline {
    position: absolute; left: 324px; top: 545px;
    font-style: italic; font-weight: 700;
    font-size: 22px; color: var(--byline-ink);
  }
  .cover-artwork {
    position: absolute; left: 0; top: 763px; width: 844px; height: 437px;
    background: linear-gradient(100deg, var(--art-coral) 0%, var(--art-red) 40%, var(--art-brown) 60%, var(--art-salmon) 100%);
  }
</style>
</head>
<body>
  <main class="guide-cover">
    <div class="top-rule"></div>

    <span class="partner-name">Pelwick</span>
    <span class="product-name">Harbowline R&amp;D</span>

    <section class="title-block">
      <h1 class="cover-title">Technology Development</h1>
      <p class="cover-subtitle">What you need to know about R&amp;D</p>
    </section>

    <p class="byline">By: Harbowline</p>

    <div class="cover-artwork" role="img" aria-label="Decorative collage of overlapping translucent squares in coral, red, brown and gray"></div>
  </main>
</body>
</html>
```